New Business Card Design Project

We require a business card design for Vexalund, a newly established Indian company.
Our focus is on the development, manufacturing, and export of a diverse array of pharmaceutical products on a global scale. The card should convey a professional appearance, as our primary markets are in Africa, China, and Southeast Asian nations.
We envision a two-sided business card, with the reverse side dedicated to a logo set against a solid color or an elegantly designed pattern. The corners should be rounded. We would appreciate seeing both horizontal and vertical design options. We trust the designer to utilize their expertise in creating this design.

The content for the business card is included in the attached Word file.

Target Market(s)

Our primary markets are in Africa, China, and Southeast Asian, Latin America, Maldives, Sri Lanka

Industry/Entity Type

Pharmaceutical Manufacturing and Export

Contact Information for Business Card

Colors

Designer to choose colors to be used in the design.

Requirements
Must have
• The reverse side of the business card features solely the logo along with the tagline, "Healing for All."
Should not have
• The logo should not exceed two instances, encompassing both the front and back sides of the card.

```html
<!DOCTYPE html>
<html lang="en">
<head>
<meta charset="UTF-8">
<title>Vexalund Business Card</title>
<link rel="stylesheet" href="https://fonts.googleapis.com/css2?family=Poppins:wght@400;600&family=Open+Sans:wght@400;600&display=swap">
<style>
  :root {
    --backdrop: #232323;
    --card: #1d1d1f;
    --card-edge: #151516;
    --brand-blue: #2b9fd8;
    --brand-red: #e45b4b;
    --text-light: #e4e4e4;
    --text-muted: #bdbdbd;
  }
  * { margin: 0; padding: 0; box-sizing: border-box; }
  html, body {
    width: 1200px;
    height: 780px;
    overflow: hidden;
    background: var(--backdrop);
  }
  .canvas {
    position: relative;
    width: 1200px;
    height: 780px;
    background: var(--backdrop);
  }
  .card {
    position: absolute;
    background: var(--card);
    border-radius: 24px;
    box-shadow: 0 6px 0 var(--card-edge), 0 18px 40px rgba(0,0,0,0.45);
    overflow: hidden;
  }

  /* Front: vertical */
  .card-front {
    left: 130px;
    top: 110px;
    width: 340px;
    height: 560px;
    padding: 46px 36px;
  }
  .wordmark {
    display: flex;
    align-items: center;
    gap: 10px;
    font-family: "Poppins", sans-serif;
    font-weight: 600;
    color: var(--brand-blue);
    letter-spacing: 0.5px;
    white-space: nowrap;
  }
  .wordmark-dot {
    border-radius: 50%;
    background: var(--brand-blue);
    flex: none;
  }
  .card-front .wordmark { font-size: 34px; justify-content: flex-end; }
  .card-front .wordmark-dot { width: 14px; height: 14px; }

  .holder {
    margin-top: 40px;
    padding-left: 12px;
    border-left: 4px solid var(--brand-blue);
  }
  .holder-name {
    font-family: "Open Sans", sans-serif;
    font-size: 22px;
    font-weight: 400;
    line-height: 1.15;
    color: var(--brand-blue);
    white-space: nowrap;
  }
  .holder-name .surname { color: var(--brand-red); }
  .holder-title {
    font-family: "Open Sans", sans-serif;
    font-size: 12px;
    color: var(--text-light);
    margin-top: 2px;
  }
  .address {
    margin-top: 24px;
    font-family: "Open Sans", sans-serif;
    font-size: 12.5px;
    line-height: 1.5;
    color: var(--text-light);
  }
  .contact-list {
    list-style: none;
    margin-top: 14px;
    font-family: "Open Sans", sans-serif;
    font-size: 12.5px;
    color: var(--text-light);
  }
  .contact-list li {
    display: flex;
    align-items: center;
    gap: 9px;
    line-height: 1.9;
    white-space: nowrap;
  }
  .contact-icon { width: 12px; height: 12px; flex: none; }

  /* Back: horizontal */
  .card-back {
    left: 560px;
    top: 220px;
    width: 540px;
    height: 340px;
    display: flex;
    flex-direction: column;
    align-items: center;
    justify-content: center;
  }
  .card-back .wordmark { font-size: 56px; }
  .card-back .wordmark-dot { width: 20px; height: 20px; }
  .tagline {
    margin-top: 8px;
    font-family: "Poppins", sans-serif;
    font-size: 15px;
    color: var(--text-muted);
    letter-spacing: 0.4px;
  }
</style>
</head>
<body>
<main class="canvas">

  <section class="card card-front" aria-label="Business card front">
    <div class="wordmark">
      <span>Vexalund</span>
      <span class="wordmark-dot"></span>
    </div>

    <div class="holder">
      <p class="holder-name">Arjun <span class="surname">K. Malvade</span></p>
      <p class="holder-title">CEO</p>
    </div>

    <p class="address">14, Sarovar Colony,<br>Nandgiri, 440210, India</p>

    <ul class="contact-list">
      <li>
        <svg class="contact-icon" viewBox="0 0 12 12" aria-hidden="true">
          <rect x="2.5" y="0.8" width="7" height="10.4" rx="1.4" fill="none" stroke="var(--brand-red)" stroke-width="1.3"/>
          <circle cx="6" cy="9.2" r="0.7" fill="var(--brand-red)"/>
        </svg>
        <span>+919 400011122</span>
      </li>
      <li>
        <svg class="contact-icon" viewBox="0 0 12 12" aria-hidden="true">
          <circle cx="6" cy="6" r="5" fill="none" stroke="var(--brand-blue)" stroke-width="1.2"/>
          <ellipse cx="6" cy="6" rx="2.2" ry="5" fill="none" stroke="var(--brand-blue)" stroke-width="1"/>
          <line x1="1" y1="6" x2="11" y2="6" stroke="var(--brand-blue)" stroke-width="1"/>
        </svg>
        <span>www.vexalund.com</span>
      </li>
      <li>
        <svg class="contact-icon" viewBox="0 0 12 12" aria-hidden="true">
          <rect x="0.8" y="2.2" width="10.4" height="7.6" rx="1" fill="none" stroke="var(--brand-red)" stroke-width="1.2"/>
          <polyline points="1,2.8 6,6.8 11,2.8" fill="none" stroke="var(--brand-red)" stroke-width="1.2"/>
        </svg>
        <span>amalvade@vexalund.com</span>
      </li>
    </ul>
  </section>

  <section class="card card-back" aria-label="Business card back">
    <div class="wordmark">
      <span>Vexalund</span>
      <span class="wordmark-dot"></span>
    </div>
    <p class="tagline">Healing for All.</p>
  </section>

</main>
</body>
</html>
```